Event Center Website

We need a new website design for an upscale event center in Reno, Nevada. The building hosts everything from weddings to corporate events to funerals and it competitively more expensive. The overall look and feel is consistent with a Lake Tahoe aesthetic. The current site can be viewed at www.themaplehallevents.com. They are looking for a major upgrade. A sample site they like is www.cliffsidelodgestay.com. We have new photography available (some attached). The site should be very visual. A site map is attached as well for direction on what elements the site should include as well as labels for navigation. I am looking for a home page and sample interior page. Any questions, let me know. Thanks.
Updates

I have added some photography of the center itself for use rather than stock photography. Thanks!

Target Market(s)

Brides, professionals, high-income

Industry/Entity Type

Building

Requirements
Must have
• See site map

```html
<!DOCTYPE html>
<html lang="en">
<head>
<meta charset="utf-8">
<title>Maple Hall – Meet Our Team</title>
<link href="https://fonts.googleapis.com/css2?family=Ubuntu:wght@400;500;700&display=swap" rel="stylesheet">
<style>
:root{
  --cream:#f6e7c5;
  --cream-panel:rgba(248,234,202,.93);
  --brown-dark:#4a2716;
  --brown:#6a3a1e;
  --brown-mid:#7d4410;
  --orange:#d0731f;
  --orange-btn:#d27a25;
  --text:#4b3222;
  --footer-bg:#f6e7c5;
}
*{box-sizing:border-box;margin:0;padding:0}
html,body{width:1200px;height:874px;overflow:hidden}
body{font-family:'Ubuntu',sans-serif;background:var(--footer-bg);position:relative;color:var(--text)}
.hero{position:absolute;left:0;top:0;width:1200px;height:708px;
  background:radial-gradient(ellipse at 50% 15%,#e8b45a 0%,#b37a35 25%,#5e3f27 55%,#2d241f 80%),#3a2a20}
.hero-floor{position:absolute;left:0;top:520px;width:1200px;height:188px;
  background:linear-gradient(#c9b2a4,#8c7566 60%,#3b2f2a)}
.utility{position:absolute;left:849px;top:0;width:227px;height:52px;background:var(--brown-dark);
  display:flex;align-items:center;justify-content:center;color:#fff;font-size:15px}
.utility a{color:#f4e3c4;text-decoration:none;padding:0 20px}
.utility .sep{width:2px;height:26px;background:#e9d6b3}
.mainnav{position:absolute;left:100px;top:52px;width:976px;height:58px;background:var(--cream);
  display:flex;align-items:center}
.brand{width:190px;padding-left:10px;font-size:26px;font-weight:500;color:var(--brown-dark);letter-spacing:.5px}
.mainnav ul{list-style:none;display:flex}
.mainnav li{font-size:15px;font-weight:500;color:var(--brown-dark);padding:0 17px;height:58px;line-height:58px}
.mainnav li.active{border-bottom:2px solid var(--brown)}
.arrow{position:absolute;top:386px;width:47px;height:47px;border-radius:50%;background:#8b4a24;opacity:.95}
.arrow.prev{left:22px}.arrow.next{left:1128px}
.arrow svg{position:absolute;left:13px;top:13px}
.modal{position:absolute;left:212px;top:188px;width:794px;height:405px;background:var(--cream-panel)}
.modal h1{font-size:25px;font-weight:500;color:var(--brown-dark);text-align:center;height:50px;line-height:52px;border-bottom:1px solid #6e5140;letter-spacing:.3px}
.close{position:absolute;left:762px;top:17px;width:22px;height:22px;border-radius:50%;background:var(--brown-dark)}
.close svg{position:absolute;left:6px;top:6px}
.member-title{position:absolute;left:0;top:58px;width:794px;text-align:center;font-size:26px;font-weight:500;color:var(--brown-dark)}
.member-title span,.caption span{color:var(--orange)}
.photo{position:absolute;left:28px;top:103px;width:235px;height:221px;border:3px solid #8a6a55;
  background:linear-gradient(160deg,#f2f2f2 0%,#d8c2b2 45%,#a9adb0 100%)}
.caption{position:absolute;left:28px;top:335px;width:235px;text-align:center;font-size:16.5px;font-weight:500;color:var(--brown-dark)}
.bio{position:absolute;left:283px;top:100px;width:468px;height:268px;overflow:hidden;font-size:13.6px;line-height:22.3px;text-align:justify;color:var(--text)}
.scroll{position:absolute;left:771px;top:61px;width:7px;height:312px;border-radius:4px;background:var(--brown-dark)}
.scroll i{position:absolute;left:2px;top:38px;width:3px;height:40px;background:var(--orange)}
.newsletter{position:absolute;left:131px;top:747px;width:340px;height:60px;background:var(--brown-mid);display:flex}
.newsletter .field{flex:1;color:#f8e7c6;font-size:14.5px;line-height:60px;padding-left:9px;position:relative}
.newsletter .field svg{position:absolute;right:10px;top:15px}
.newsletter .send{width:56px;background:var(--orange-btn);color:#fff;font-size:14.5px;line-height:60px;text-align:center}
.contact{position:absolute;left:495px;top:748px;width:362px;height:58px;background:var(--brown-dark);display:flex;font-size:13px;color:#f4e3c4}
.contact .addr{width:130px;padding:9px 0 0 11px;line-height:21px;border-right:1px solid #7a5238;white-space:nowrap}
.contact .info{flex:1;padding:7px 0 0 9px;line-height:22px;font-size:12px;white-space:nowrap}
.contact .info b{font-weight:400;color:var(--orange)}
.social{position:absolute;left:887px;top:748px;width:189px;height:60px;background:#6f3918;display:flex;gap:10px;align-items:center;justify-content:center}
.social span{width:30px;height:30px}
.footnav{position:absolute;left:0;top:834px;width:1200px;display:flex;justify-content:center;list-style:none;font-size:14px;color:var(--brown-dark)}
.footnav li{padding:0 14px}
</style>
</head>
<body>
<div class="hero" role="img" aria-label="Photograph of the event hall interior with draped ceiling, chandelier and rows of white chairs along an aisle"><div class="hero-floor"></div></div>

<nav class="utility"><a>FAQ</a><span class="sep"></span><a>TESTIMONIAL</a></nav>
<header class="mainnav">
  <div class="brand">maple hall</div>
  <ul>
    <li class="active">ABOUT US</li><li>GALLERY</li><li>WEDDING</li><li>MEETINGS</li><li>OTHER EVENTS</li><li>CATERING</li><li>MENUS</li>
  </ul>
</header>

<div class="arrow prev"><svg width="21" height="21" viewBox="0 0 21 21"><path d="M10 3 3 10.5 10 18M18 3 11 10.5 18 18" fill="none" stroke="#fff" stroke-width="2.4"/></svg></div>
<div class="arrow next"><svg width="21" height="21" viewBox="0 0 21 21"><path d="M3 3 10 10.5 3 18M11 3 18 10.5 11 18" fill="none" stroke="#fff" stroke-width="2.4"/></svg></div>

<section class="modal">
  <h1>MEET OUR TEAM</h1>
  <div class="close"><svg width="10" height="10" viewBox="0 0 10 10"><path d="M1 1 9 9M9 1 1 9" stroke="#fff" stroke-width="2.4"/></svg></div>
  <h2 class="member-title">Dana, <span>General Manager</span></h2>
  <div class="photo" role="img" aria-label="Portrait photo of the general manager"></div>
  <p class="caption">Dana, <span>General Manager</span></p>
  <p class="bio">Dana grew up in Reno and has many ties to the Reno community. Her love for event planning and becoming a “foodie” started many years ago when she became Event Director and Assistant Manager at The Aspen Ridge Club. Planning events and creating menus became a passion and has followed her throughout her career. Having been a part of event planning, catering and management for more than two decades, Maple Hall is the perfect fit for Dana. Her philosophy for managing a successful venue is creating a professional, inviting atmosphere where guests will enjoy amazing food served by welcoming staff. Dana’s team shares a passion for food and quality of service. They want to ensure that every event is special and successful. Their goal is create the perfect setting for a memorable event. Dana is also the Director of Sales and loves working with our clients. Planning a fun fashion show, a gala dinner or an intimate wedding is what she enjoys most.</p>
  <div class="scroll"><i></i></div>
</section>

<form class="newsletter">
  <div class="field">ENTER YOUR EMAIL
    <svg width="32" height="30" viewBox="0 0 32 30"><path d="M1 12 16 2 31 12V29H1Z M1 12 16 22 31 12" fill="none" stroke="#fff" stroke-width="1.6"/></svg>
  </div>
  <div class="send">SEND</div>
</form>
<div class="contact">
  <div class="addr">48 Ridgeview Lane<br>Reno, NV 89509</div>
  <div class="info"><b>Phone:</b>&nbsp; 775-555-0142<br><b>Email:</b>&nbsp; info@themaplehallevents.com</div>
</div>
<div class="social">
  <span style="background:#3b5a9a" aria-label="Social link"></span>
  <span style="background:#2fa8e0" aria-label="Social link"></span>
  <span style="background:#c4302b" aria-label="Video link"></span>
  <span style="background:#f07a22" aria-label="Feed link"></span>
</div>
<ul class="footnav"><li>ABOUT US</li><li>GALLERY</li><li>WEDDING</li><li>MEETINGS</li><li>OTHER EVENTS</li><li>CATERING</li><li>MENUS</li></ul>
</body>
</html>
```